Im open to ideas.. I was thinking on my business cards aswell as my logo. a place for my name. email. phone number and abn..

ive attched a file with my business logo. which i dont love the colours.. i was think a dark background with charcoal letters so something along those colour schumes but im open to ideas..

BRM Constructions

```html
<!DOCTYPE html>
<html lang="en">
<head>
<meta charset="utf-8">
<title>BRM Constructions – Business Card</title>
<link rel="stylesheet" href="https://fonts.googleapis.com/css2?family=Montserrat:wght@400;500;600;700&display=swap">
<style>
  :root {
    --page-bg: #d8d2c8;
    --card-white: #fbfbfa;
    --card-black: #0b0b0b;
    --brand-red: #e8313a;
    --ink-charcoal: #2b2b2b;
    --text-light: #f2f2f2;
  }
  * { box-sizing: border-box; margin: 0; padding: 0; }
  html, body {
    width: 1200px; height: 1022px; overflow: hidden;
    background: var(--page-bg);
    font-family: "Montserrat", sans-serif;
  }
  .sheet {
    position: relative; width: 1200px; height: 1022px;
    display: flex; align-items: center; justify-content: center; gap: 60px;
  }
  .card {
    position: relative; width: 525px; height: 300px;
    border-radius: 14px; overflow: hidden;
    box-shadow: 0 10px 28px rgba(0,0,0,.25);
  }
  /* Front */
  .card-front { background: var(--card-white); }
  .front-rule {
    position: absolute; left: 0; top: 0; width: 100%; height: 40px;
  }
  .brand-name {
    position: absolute; left: 0; right: 0; top: 128px;
    display: flex; align-items: center; justify-content: center; gap: 14px;
    font-weight: 700; font-size: 34px; letter-spacing: 1px;
    color: var(--ink-charcoal); text-transform: uppercase;
  }
  .brand-mark {
    width: 22px; height: 22px; background: var(--brand-red);
  }
  /* Back */
  .card-back { background: var(--card-black); color: var(--text-light); }
  .details { position: absolute; left: 52px; top: 60px; }
  .person-name {
    font-weight: 600; font-size: 30px; letter-spacing: 1px;
    color: var(--brand-red); text-transform: uppercase;
  }
  .person-role { font-size: 17px; margin-top: 4px; }
  .abn { font-size: 17px; margin-top: 14px; }
  .abn-label { color: var(--brand-red); font-weight: 600; }
  .contact-list { list-style: none; margin-top: 8px; }
  .contact-item {
    display: flex; align-items: center; gap: 12px;
    font-size: 17px; line-height: 30px;
  }
  .contact-icon { width: 14px; height: 14px; flex: none; }
</style>
</head>
<body>
<main class="sheet">
  <section class="card card-front" aria-label="Card front">
    <svg class="front-rule" viewBox="0 0 525 40" aria-hidden="true">
      <polyline points="0,24 150,24 162,10 174,24 525,24" fill="none" stroke="var(--brand-red)" stroke-width="2"/>
      <polyline points="0,29 150,29 162,15 174,29 525,29" fill="none" stroke="var(--brand-red)" stroke-width="1"/>
    </svg>
    <div class="brand-name"><span class="brand-mark"></span>BRM Constructions</div>
  </section>

  <section class="card card-back" aria-label="Card back">
    <div class="details">
      <h1 class="person-name">Daniel Porter</h1>
      <p class="person-role">Director</p>
      <p class="abn"><span class="abn-label">ABN</span>: 61 402 735 219</p>
      <ul class="contact-list">
        <li class="contact-item">
          <svg class="contact-icon" viewBox="0 0 16 16" aria-hidden="true"><path d="M3 1l3 3-2 2c1 2 3 4 5 5l2-2 3 3-2 3C6 15 1 10 1 3z" fill="var(--brand-red)"/></svg>
          +330 2460-1184
        </li>
        <li class="contact-item">
          <svg class="contact-icon" viewBox="0 0 16 16" aria-hidden="true"><rect x="1" y="3" width="14" height="10" fill="none" stroke="var(--brand-red)" stroke-width="1.6"/><polyline points="1,3 8,9 15,3" fill="none" stroke="var(--brand-red)" stroke-width="1.6"/></svg>
          info@brmconstructions.com
        </li>
        <li class="contact-item">
          <svg class="contact-icon" viewBox="0 0 16 16" aria-hidden="true"><circle cx="8" cy="8" r="7" fill="var(--brand-red)"/><path d="M1 8h14M8 1c-3 4-3 10 0 14M8 1c3 4 3 10 0 14" fill="none" stroke="var(--card-black)" stroke-width="1"/></svg>
          www.brmconstructions.com
        </li>
      </ul>
    </div>
  </section>
</main>
</body>
</html>
```